Business Card Design

I am an Event and Wedding Planner in need of an eye catching business card featuring my logo (attached), my contact details, and my company tagline (Making every celebration glow with wonder...) I would like the tagline in font similar the logo's font.
Updates
I have just noticed that my logo has a misspelling so for the final design, I will be uploading a corrected logo as soon as I have it.
My apologies.
Reason: Waiting on a corrected logo...Lantern is misspelled and it should say Weddings not Wedding
The logo has been corrected so now Lantern is spelled correctly and it says Weddings instead of Wedding. Please use Edwardian Script ITC as the font for the tagline so it will match the logo. Thank you for your patience.
Target Market(s)
Engaged couples and people hosting milestone celebrations. 25-50 years old, predominately female
Industry/Entity Type
Business
Contact Information for Business Card
Rosalind Merrow, Event Manager / Owner, Mobile: 0491 868 254, Email: rosalind@velvetlanternco.com.au, www.velvetlanternco.com.au, Making every celebration glow with wonder...

```html
<!DOCTYPE html>
<html lang="en">
<head>
<meta charset="utf-8">
<title>Velvet Lantern Co. – Business Card</title>
<link rel="stylesheet" href="https://fonts.googleapis.com/css2?family=EB+Garamond:wght@400;500&family=Pinyon+Script&display=swap">
<style>
  :root {
    --backdrop: #1e1d1d;
    --card-white: #fbfbfa;
    --accent-red: #c8211f;
    --ink: #1c1c1c;
    --photo-grey-light: #e6e6e4;
    --photo-grey-mid: #b9b9b7;
    --photo-rose-red: #9e1d14;
    --photo-rose-deep: #5e0f0a;
    --photo-cream: #efe4cf;
    --photo-pink: #d9a9b4;
    --band-grey: rgba(80, 80, 80, 0.72);
    --text-white: #ffffff;
  }
  * { box-sizing: border-box; margin: 0; padding: 0; }
  html, body {
    width: 1200px;
    height: 900px;
    overflow: hidden;
    background: var(--backdrop);
  }
  .canvas {
    position: relative;
    width: 1200px;
    height: 900px;
  }
  .card {
    position: absolute;
    left: 260px;
    width: 680px;
    height: 389px;
    overflow: hidden;
    box-shadow: 0 10px 30px rgba(0,0,0,0.55);
  }
  .card--front { top: 48px; background: var(--card-white); }
  .card--back  { top: 463px; }

  /* Front */
  .front-art {
    position: absolute;
    inset: 0;
    width: 100%;
    height: 100%;
  }
  .tagline {
    position: absolute;
    left: 26px;
    top: 258px;
    width: 260px;
    font-family: "Pinyon Script", cursive;
    font-size: 25px;
    line-height: 1.15;
    color: var(--ink);
    transform: rotate(14deg);
    transform-origin: left top;
  }
  .front-info {
    position: absolute;
    left: 360px;
    top: 52px;
    width: 300px;
    text-align: center;
    font-family: "EB Garamond", serif;
  }
  .brand {
    display: inline-flex;
    align-items: center;
    gap: 8px;
    font-size: 26px;
    font-weight: 400;
    color: var(--ink);
    padding-bottom: 6px;
    border-bottom: 1px solid #555;
  }
  .brand__dot {
    width: 10px;
    height: 10px;
    border-radius: 50%;
    background: var(--accent-red);
  }
  .person-name {
    margin-top: 30px;
    font-size: 36px;
    font-weight: 400;
    color: var(--accent-red);
    line-height: 1;
  }
  .person-role {
    margin-top: 6px;
    font-size: 15px;
    color: var(--accent-red);
  }
  .contact {
    margin-top: 58px;
    font-size: 16px;
    line-height: 1.45;
    color: var(--accent-red);
  }

  /* Back */
  .back-photo {
    position: absolute;
    inset: 0;
    background:
      radial-gradient(ellipse at 30% 72%, var(--photo-cream) 0%, rgba(239,228,207,0) 32%),
      radial-gradient(ellipse at 14% 55%, var(--photo-pink) 0%, rgba(217,169,180,0) 30%),
      radial-gradient(ellipse at 78% 38%, var(--photo-rose-red) 0%, rgba(158,29,20,0) 45%),
      linear-gradient(135deg, var(--photo-rose-deep) 0%, var(--photo-rose-red) 45%, #7a1a14 70%, #3d3a36 100%);
  }
  .back-brand {
    position: absolute;
    left: 34px;
    top: 34px;
    display: flex;
    align-items: center;
    gap: 8px;
    font-family: "EB Garamond", serif;
    font-size: 28px;
    color: var(--text-white);
    padding-bottom: 6px;
    border-bottom: 1px solid rgba(255,255,255,0.8);
  }
  .back-brand__dot {
    width: 10px;
    height: 10px;
    border-radius: 50%;
    border: 1.5px solid var(--text-white);
  }
  .back-band {
    position: absolute;
    left: 0;
    right: 0;
    bottom: 30px;
    height: 56px;
    background: var(--band-grey);
    display: flex;
    align-items: center;
    justify-content: flex-end;
    padding-right: 30px;
    font-family: "EB Garamond", serif;
    font-size: 23px;
    color: var(--text-white);
  }
</style>
</head>
<body>
<main class="canvas">

  <section class="card card--front" aria-label="Business card front">
    <svg class="front-art" viewBox="0 0 680 389" preserveAspectRatio="none">
      <defs>
        <linearGradient id="bouquetTone" x1="0" y1="0" x2="1" y2="1">
          <stop offset="0" stop-color="#f2f2f0"/>
          <stop offset="0.45" stop-color="#c9c9c6"/>
          <stop offset="0.7" stop-color="#eeeedf"/>
          <stop offset="1" stop-color="#a9a9a7"/>
        </linearGradient>
      </defs>
      <path role="img" aria-label="Photograph of a bride holding a white rose and calla lily bouquet"
            d="M0 0 H470 C440 140 330 290 140 389 H0 Z" fill="url(#bouquetTone)"/>
      <path d="M470 0 C440 140 330 290 140 389" fill="none" stroke="#111" stroke-width="3"/>
    </svg>
    <p class="tagline">Making every celebration glow with wonder...</p>
    <div class="front-info">
      <div class="brand"><span>Velvet Lantern Co.</span><span class="brand__dot"></span></div>
      <h1 class="person-name">Rosalind Merrow</h1>
      <p class="person-role">Event Manager</p>
      <p class="contact">www.velvetlanternco.com.au<br>0491 868 254</p>
    </div>
  </section>

  <section class="card card--back" aria-label="Business card back">
    <div class="back-photo" role="img" aria-label="Photograph of red and cream roses with baby's breath beside a pink ring box"></div>
    <div class="back-brand"><span>Velvet Lantern Co.</span><span class="back-brand__dot"></span></div>
    <div class="back-band">rosalind@velvetlanternco.com.au</div>
  </section>

</main>
</body>
</html>
```